RW Framewell Inc Business cards

We need business cards using our existing logo but slightly modified. Right now the logo says RW Loadbearing Masonry. We want to keep the RW part of the design, but replace the Structural Concrete portion with "FRAMEWELL". Please see the attached file.
Ideally this would be a blank template so we can add Different Names, titles, and phone numbers later.
On the one side we want only the logo and on the other side the detail. I'm attaching an example for you to see.
Please reach out with any other questions. Our address and other details will be given out once we find a design we like.

Target Market(s)

Construction Industry

```html
<!DOCTYPE html>
<html lang="en">
<head>
<meta charset="UTF-8">
<title>RW Framewell Inc – Business Cards</title>
<link href="https://fonts.googleapis.com/css2?family=Montserrat:wght@400;500;700&family=Roboto:wght@400;500&display=swap" rel="stylesheet">
<style>
  :root {
    --brand-blue: #0f7cc8;
    --brand-blue-deep: #0a67b2;
    --ink-grey: #4a4a4a;
    --rule-grey: #9a9a9a;
    --paper: #ffffff;
    --backdrop: #dcdcda;
  }
  * { margin: 0; padding: 0; box-sizing: border-box; }
  html, body { width: 1200px; height: 801px; overflow: hidden; }
  body {
    background: var(--backdrop);
    position: relative;
    font-family: "Roboto", Arial, sans-serif;
  }
  .card {
    position: absolute;
    top: 246px;
    width: 540px;
    height: 309px;
    overflow: hidden;
    box-shadow: 0 10px 24px rgba(0,0,0,0.18);
  }
  /* Detail side */
  .card-front { left: 40px; background: var(--paper); }
  .front-wordmark {
    position: absolute;
    left: 34px;
    top: 96px;
    width: 200px;
    display: flex;
    align-items: center;
    gap: 10px;
    font-family: "Montserrat", Arial, sans-serif;
    font-weight: 700;
    color: var(--brand-blue);
    font-size: 21px;
    letter-spacing: 1.5px;
  }
  .wordmark-square {
    width: 14px; height: 14px;
    background: var(--brand-blue);
    flex: none;
  }
  .divider {
    position: absolute;
    left: 250px;
    top: 58px;
    width: 1.5px;
    height: 122px;
    background: var(--rule-grey);
  }
  .contact {
    position: absolute;
    left: 274px;
    top: 52px;
    color: var(--ink-grey);
  }
  .contact-name {
    font-family: "Montserrat", Arial, sans-serif;
    font-weight: 700;
    font-size: 22px;
    color: var(--brand-blue);
    line-height: 1.1;
  }
  .contact-title { font-size: 15px; margin-bottom: 12px; }
  .contact-line {
    display: flex;
    align-items: center;
    gap: 7px;
    font-size: 15px;
    line-height: 22px;
  }
  .contact-line svg { width: 13px; height: 13px; flex: none; }
  .address-band {
    position: absolute;
    left: 0; right: 0;
    top: 228px;
    height: 46px;
    background: var(--brand-blue-deep);
    color: var(--paper);
    display: flex;
    align-items: center;
    justify-content: center;
    gap: 8px;
    font-size: 15px;
    letter-spacing: 0.2px;
  }
  .address-band svg { width: 12px; height: 16px; }
  /* Logo side */
  .card-back {
    left: 620px;
    background: linear-gradient(160deg, var(--brand-blue) 0%, var(--brand-blue-deep) 100%);
    display: flex;
    align-items: center;
    justify-content: center;
  }
  .back-wordmark {
    display: flex;
    align-items: center;
    gap: 16px;
    font-family: "Montserrat", Arial, sans-serif;
    font-weight: 700;
    color: var(--paper);
    font-size: 38px;
    letter-spacing: 3px;
  }
  .back-wordmark .wordmark-square { width: 24px; height: 24px; background: var(--paper); }
</style>
</head>
<body>

<section class="card card-front" aria-label="Business card, detail side">
  <div class="front-wordmark"><span class="wordmark-square"></span>RW FRAMEWELL</div>
  <div class="divider"></div>
  <div class="contact">
    <p class="contact-name">Dana Whitlock</p>
    <p class="contact-title">Director</p>
    <p class="contact-line">
      <svg viewBox="0 0 16 16" aria-hidden="true"><circle cx="8" cy="8" r="8" fill="#0f7cc8"/><path d="M5 4.5c.6-.3 1.2 0 1.4.6l.4 1c.1.4 0 .7-.3.9l-.5.3c.4.9 1.1 1.6 2 2l.3-.5c.2-.3.5-.4.9-.3l1 .4c.6.2.9.8.6 1.4-.4.9-1.4 1.2-2.3.8A7 7 0 0 1 4.4 6.8c-.4-.9-.1-1.9.6-2.3z" fill="#fff"/></svg>
      555.014.2270
    </p>
    <p class="contact-line">
      <svg viewBox="0 0 16 16" aria-hidden="true"><circle cx="8" cy="8" r="8" fill="#0f7cc8"/><rect x="4" y="5" width="8" height="6" fill="#fff"/><path d="M4 5l4 3.4L12 5" stroke="#0f7cc8" stroke-width="0.9" fill="none"/></svg>
      info@rwframewell.com
    </p>
    <p class="contact-line">
      <svg viewBox="0 0 16 16" aria-hidden="true"><circle cx="8" cy="8" r="8" fill="#0f7cc8"/><circle cx="8" cy="8" r="4.4" fill="none" stroke="#fff" stroke-width="1"/><ellipse cx="8" cy="8" rx="1.8" ry="4.4" fill="none" stroke="#fff" stroke-width="0.9"/><path d="M3.6 8h8.8" stroke="#fff" stroke-width="0.9"/></svg>
      www.rwframewell.com
    </p>
  </div>
  <div class="address-band">
    <svg viewBox="0 0 12 16" aria-hidden="true"><path d="M6 0a6 6 0 0 0-6 6c0 4.5 6 10 6 10s6-5.5 6-10a6 6 0 0 0-6-6z" fill="#fff"/><circle cx="6" cy="6" r="2.2" fill="#0a67b2"/></svg>
    Granite Avenue, Suite 210 Harbor Point, California 90210
  </div>
</section>

<section class="card card-back" aria-label="Business card, logo side">
  <div class="back-wordmark"><span class="wordmark-square"></span>RW FRAMEWELL</div>
</section>

</body>
</html>
```